Calden L - Premium Business Cards

Background of Calden L
Calden Leafworks is a cigar mobile lounge where guests become family. A place of luxury, relaxation, and ambiance is the global popularity demand. Calden Leafworks strives to provide first-class service of quality and products. Our goal is to ensure that every guest is treated and serviced as a VIP.

Calden Leafworks was founded by Dennis Markow Jr in January 2020. After 15 years of cigar reviews and research Dennis decided it was time to launch his own cigar brand and boutique cigar company. With a wealth of knowledge and years of experience Calden Leafworks was born. With opulence for all cultures, Calden Leafworks offers hand rolled cigars with premium blend tobacco from sweet to bold imported from Costa Rica, Dominican Republic, and Nicaragua. Thank you for your business!

Objective:
Create a business card template to be used for all employees. Design should communicate premium and classy. And should use earth tone colors.

Design should include:
1. Client wants to incorporate the cigar leaf
2. Logo
3. Tagline: Savor every draw
3. Content info:
Kevin Oldacre
Owner
555-017-4863
koldacre@caldenleaf.com
caldenleafworks.com

```html
<!DOCTYPE html>
<html lang="en">
<head>
<meta charset="utf-8">
<title>Calden Leafworks – Business Cards</title>
<link href="https://fonts.googleapis.com/css2?family=Lato:wght@400;700&family=Oswald:wght@500&display=swap" rel="stylesheet">
<style>
  :root {
    --stage: #a6a6a6;
    --ink: #231f20;
    --paper: #ffffff;
    --smoke-light: #f2f2f2;
    --smoke-dark: #cfcfcf;
  }
  * { margin: 0; padding: 0; box-sizing: border-box; }
  html, body { width: 1075px; height: 1200px; overflow: hidden; }
  body { background: var(--stage); position: relative; font-family: "Lato", sans-serif; }

  .card {
    position: absolute;
    width: 663px;
    height: 395px;
    box-shadow: 3px 3px 3px rgba(0,0,0,0.55);
    overflow: hidden;
  }
  .card--front { left: 206px; top: 187px; background: var(--paper); }
  .card--back  { left: 204px; top: 638px; background: var(--ink); color: var(--paper); }

  .smoke-art {
    position: absolute; left: 31px; top: 6px; width: 578px; height: 117px;
    background: linear-gradient(100deg, var(--paper) 0%, var(--smoke-light) 35%, var(--smoke-dark) 75%, var(--smoke-light) 100%);
    border-radius: 40px;
  }
  .cigar-art {
    position: absolute; left: 576px; top: 150px; width: 46px; height: 231px;
    background: linear-gradient(180deg, #555 0%, var(--ink) 100%);
    border-radius: 4px 4px 23px 23px;
  }

  .info-band {
    position: absolute; left: 0; top: 195px; width: 562px; height: 169px;
    background: var(--ink); color: var(--paper);
  }
  .person-name {
    position: absolute; left: 36px; top: 17px;
    font-weight: 700; font-size: 23px; letter-spacing: 0.2px; line-height: 1.1;
  }
  .person-role {
    position: absolute; left: 36px; top: 42px;
    font-weight: 400; font-size: 18px; line-height: 1.1;
  }
  .contact-list { list-style: none; position: absolute; left: 36px; top: 78px; }
  .contact-list li {
    display: flex; align-items: center; height: 24px;
    font-family: Arial, Helvetica, sans-serif; font-size: 19px;
  }
  .contact-list svg { width: 16px; height: 16px; margin-right: 7px; flex: none; }

  .brand-name {
    position: absolute; left: 0; width: 100%; top: 183px; text-align: center;
    font-family: "Lato", sans-serif; font-weight: 700; font-size: 44px; letter-spacing: 2px;
    text-transform: uppercase;
  }
  .tagline {
    position: absolute; left: 0; width: 100%; top: 320px; text-align: center;
    font-family: "Oswald", sans-serif; font-weight: 500; font-size: 25px; letter-spacing: 2.5px;
  }
</style>
</head>
<body>

<section class="card card--front">
  <div class="smoke-art" role="img" aria-label="Flowing cigar smoke illustration"></div>
  <div class="cigar-art" role="img" aria-label="Cigar with wrapper leaf illustration"></div>

  <div class="info-band">
    <h1 class="person-name">KEVIN OLDACRE</h1>
    <p class="person-role">Owner</p>
    <ul class="contact-list">
      <li>
        <svg viewBox="0 0 16 16" aria-hidden="true"><path fill="#fff" d="M3.5 1.5l2.3 2.8-1.4 1.7c.9 2 2.6 3.7 4.6 4.6l1.7-1.4 2.8 2.3-1.3 2.1C7 14.8 1.2 9 1.4 2.8z"/></svg>
        555-017-4863
      </li>
      <li>
        <svg viewBox="0 0 16 16" aria-hidden="true"><rect x="1" y="3" width="14" height="10" fill="#fff"/><path d="M1 3l7 6 7-6" fill="none" stroke="#231f20" stroke-width="1.3"/></svg>
        koldacre@caldenleaf.com
      </li>
      <li>
        <svg viewBox="0 0 16 16" aria-hidden="true"><g fill="none" stroke="#fff" stroke-width="1.3"><circle cx="8" cy="8" r="6.5"/><ellipse cx="8" cy="8" rx="2.8" ry="6.5"/><path d="M1.5 8h13M2.5 4.8h11M2.5 11.2h11"/></g></svg>
        caldenleafworks.com
      </li>
    </ul>
  </div>
</section>

<section class="card card--back">
  <p class="brand-name">Calden Leafworks</p>
  <p class="tagline">SAVOR EVERY DRAW</p>
</section>

</body>
</html>
```